New Webpage for High Class Expert Witness Services Company

We are looking for a minimalist design for a webpage that just has our logo and an entry form offer to connect with one of our Liaisons.
The entry form should just ask for Name, Email, Contact Info and Description of Project.

Company Name is: The Marlowe Crest Advisory Services

Number of Pages Required

1 page

```html
<!DOCTYPE html>
<html lang="en">
<head>
<meta charset="UTF-8">
<title>Marlowe Crest Advisory Services — Inquiry</title>
<link href="https://fonts.googleapis.com/css2?family=Playfair+Display:wght@700&family=Cinzel:wght@400&family=Figtree:wght@300;400;500&display=swap" rel="stylesheet">
<style>
  :root {
    --ink: #111111;
    --muted: #2b2b2b;
    --label: #6f6f74;
    --panel: #f2f2f4;
    --field-border: #d6d6da;
    --accent: #6e5a36;
    --white: #ffffff;
  }
  * { margin: 0; padding: 0; box-sizing: border-box; }
  html, body { width: 1200px; height: 675px; overflow: hidden; background: var(--white); }
  body { position: relative; font-family: "Figtree", sans-serif; color: var(--ink); }

  .brand {
    position: absolute; left: 57px; top: 48px;
    display: flex; align-items: center; gap: 10px;
  }
  .brand-mark { width: 14px; height: 14px; background: var(--ink); }
  .brand-name {
    font-family: "Playfair Display", serif; font-weight: 700;
    font-size: 19px; letter-spacing: 0.02em; color: var(--ink);
  }

  .hero { position: absolute; left: 54px; top: 183px; }
  .hero-eyebrow { font-weight: 300; font-size: 16px; margin-left: 0; color: var(--muted); }
  .hero-title {
    font-family: "Playfair Display", serif; font-weight: 700;
    font-size: 76px; line-height: 73.5px; margin-top: 22px; color: var(--ink);
  }
  .hero-tagline { font-weight: 300; font-size: 16px; margin-top: 16px; color: var(--muted); }

  .copyright {
    position: absolute; left: 54px; top: 645px;
    font-weight: 300; font-size: 10px; text-transform: uppercase; color: var(--muted);
    display: flex; align-items: center; gap: 4px;
  }

  .inquiry {
    position: absolute; left: 711px; top: 126px; width: 443px; height: 549px;
    background: var(--panel);
  }
  .inquiry-title {
    position: absolute; left: 36px; top: 22px;
    font-family: "Cinzel", serif; font-size: 25px; color: var(--ink);
  }
  .inquiry-subtitle {
    position: absolute; left: 36px; top: 53px; font-weight: 300; font-size: 13px; color: var(--muted);
  }
  .field { position: absolute; left: 37px; width: 370px; }
  .field-label { display: block; font-size: 11px; color: var(--label); margin-bottom: 3px; }
  .field-input {
    display: block; width: 100%; height: 34px;
    border: 1px solid var(--field-border); background: transparent;
  }
  .field-input.area { height: 86px; }
  .submit {
    position: absolute; left: 37px; top: 378px; width: 370px; height: 44px;
    border: none; background: var(--accent); color: var(--white);
    font-family: "Figtree", sans-serif; font-weight: 500; font-size: 14px;
  }
  .privilege {
    position: absolute; left: 0; width: 100%; top: 432px; text-align: center;
    font-weight: 300; font-size: 12px; color: var(--muted);
  }
  .legal-links {
    position: absolute; left: 76px; top: 519px; display: flex; gap: 13px;
    font-weight: 300; font-size: 10px; text-transform: uppercase; color: var(--muted);
  }
</style>
</head>
<body>
  <header class="brand">
    <span class="brand-mark"></span>
    <span class="brand-name">MARLOWE CREST ADVISORY SERVICES</span>
  </header>

  <section class="hero">
    <p class="hero-eyebrow">Institutional Defense</p>
    <h1 class="hero-title">The Final<br>Word in Legal<br>Defense.</h1>
    <p class="hero-tagline">Discreet. Intelligent. Authoritative.</p>
  </section>

  <footer class="copyright">
    <svg width="10" height="10" viewBox="0 0 10 10" aria-hidden="true">
      <circle cx="5" cy="5" r="4.2" fill="none" stroke="currentColor" stroke-width="0.9"/>
      <path d="M6.4 3.7A1.8 1.8 0 1 0 6.4 6.3" fill="none" stroke="currentColor" stroke-width="0.9"/>
    </svg>
    2026 The Curated Briefing. The Silent Authority.
  </footer>

  <aside class="inquiry">
    <h2 class="inquiry-title">Inquiry Protocol</h2>
    <p class="inquiry-subtitle">Secure Consultation Request</p>

    <div class="field" style="top:87px"><span class="field-label">Full Name</span><div class="field-input"></div></div>
    <div class="field" style="top:145px"><span class="field-label">Email</span><div class="field-input"></div></div>
    <div class="field" style="top:203px"><span class="field-label">Contact Number</span><div class="field-input"></div></div>
    <div class="field" style="top:261px"><span class="field-label">Description of Project</span><div class="field-input area"></div></div>

    <button class="submit">REQUEST CONSULTATION</button>
    <p class="privilege">This communication is protected by privilege.</p>

    <nav class="legal-links">
      <span>Legal Intelligence</span>
      <span>Privacy Policy</span>
      <span>Security Protocol</span>
    </nav>
  </aside>
</body>
</html>
```